RTavenor Business Cards & Letterhead

I have a logo but need a design for some new business cards. We are a Design-Build Firm that specializes in the design and construction of commercial projects.
the cards need to be professional. no cartoon stuff.
i would like to have the cards in AI format so I can update the card as needed. Logo is provided.
Our Address is: 4187 Marlowe Ct. Cedar Hollow, Vermont 27614

```html
<!DOCTYPE html>
<html lang="en">
<head>
<meta charset="utf-8">
<title>RTavenor Business Card</title>
<link href="https://fonts.googleapis.com/css2?family=Open+Sans:wght@400;600;700;800&display=swap" rel="stylesheet">
<style>
  :root {
    --page: #e6e7ea;
    --card: #ffffff;
    --blue-deep: #0b3f6e;
    --blue: #1664a8;
    --blue-bright: #1f7fc6;
    --grey: #6f7174;
    --ink: #1a1a1a;
    --rule: #3a3a3a;
  }
  * { box-sizing: border-box; margin: 0; padding: 0; }
  html, body { width: 1200px; height: 780px; overflow: hidden; }
  body {
    background: var(--page);
    font-family: "Open Sans", Arial, sans-serif;
    position: relative;
  }
  .card {
    position: absolute;
    top: 230px;
    width: 560px;
    height: 320px;
    border-radius: 22px;
    overflow: hidden;
    background: var(--card);
    box-shadow: 0 14px 30px rgba(0,0,0,.18);
  }
  .card--front { left: 25px; }
  .card--back { left: 615px; }
  .card__swoosh { position: absolute; inset: 0; width: 100%; height: 100%; }

  .front__brand {
    position: absolute;
    inset: 0;
    display: flex; align-items: center; justify-content: center; gap: 14px;
  }
  .front__square {
    width: 34px; height: 34px; border-radius: 4px;
    background: var(--blue);
  }
  .front__name {
    font-weight: 800; font-size: 54px; letter-spacing: 1px;
    color: var(--grey); text-transform: uppercase;
  }

  .back__mark {
    position: absolute; left: 92px; top: 78px; width: 120px;
    display: flex; flex-direction: column; align-items: center; gap: 10px;
  }
  .back__square {
    width: 110px; height: 110px; border-radius: 12px;
    background: linear-gradient(145deg, var(--blue-bright), var(--blue-deep));
  }
  .back__mark-name {
    font-weight: 700; font-size: 15px; color: var(--blue); letter-spacing: .5px;
  }
  .back__divider {
    position: absolute; left: 250px; top: 70px; width: 1px; height: 150px;
    background: var(--rule);
  }
  .back__info { position: absolute; left: 268px; top: 72px; }
  .back__name {
    font-weight: 800; font-size: 24px; color: var(--blue);
    text-transform: uppercase; line-height: 1.1; letter-spacing: .3px;
  }
  .back__title { font-weight: 600; font-size: 14px; color: var(--ink); margin-bottom: 12px; }
  .contact { list-style: none; }
  .contact__item {
    display: flex; align-items: center; gap: 8px;
    font-size: 13.5px; color: var(--ink); line-height: 1.55;
  }
  .contact__icon { width: 13px; height: 13px; flex: none; }
  .back__address {
    position: absolute; left: 0; right: 0; bottom: 40px;
    text-align: center; font-size: 14px; color: var(--ink);
  }
</style>
</head>
<body>

<section class="card card--front">
  <svg class="card__swoosh" viewBox="0 0 560 320" preserveAspectRatio="none" aria-hidden="true">
    <defs>
      <linearGradient id="swoosh-front" x1="0" y1="0" x2="1" y2="1">
        <stop offset="0" stop-color="#1f7fc6"/>
        <stop offset="1" stop-color="#0b3f6e"/>
      </linearGradient>
    </defs>
    <rect width="560" height="320" fill="url(#swoosh-front)"/>
    <ellipse cx="280" cy="160" rx="262" ry="250" fill="#ffffff"/>
  </svg>
  <div class="front__brand">
    <span class="front__square"></span>
    <span class="front__name">RTavenor</span>
  </div>
</section>

<section class="card card--back">
  <svg class="card__swoosh" viewBox="0 0 560 320" preserveAspectRatio="none" aria-hidden="true">
    <defs>
      <linearGradient id="swoosh-back" x1="0" y1="0" x2="1" y2="1">
        <stop offset="0" stop-color="#1f7fc6"/>
        <stop offset="1" stop-color="#0b3f6e"/>
      </linearGradient>
    </defs>
    <rect width="560" height="320" fill="url(#swoosh-back)"/>
    <ellipse cx="280" cy="160" rx="262" ry="250" fill="#ffffff"/>
  </svg>

  <div class="back__mark">
    <span class="back__square"></span>
    <span class="back__mark-name">RTavenor</span>
  </div>

  <span class="back__divider"></span>

  <div class="back__info">
    <h1 class="back__name">Marcus Tavenor</h1>
    <p class="back__title">Founder/President</p>
    <ul class="contact">
      <li class="contact__item">
        <svg class="contact__icon" viewBox="0 0 16 16" aria-hidden="true"><path fill="#1664a8" d="M3.6 1.5l2.3 2.6-1.3 1.6c.9 2 2.6 3.7 4.7 4.7l1.6-1.3 2.6 2.3-1.2 2.1C7.6 13.6 2.4 8.4 1.5 3.7z"/></svg>
        (555) 204-0148
      </li>
      <li class="contact__item">
        <svg class="contact__icon" viewBox="0 0 16 16" aria-hidden="true"><circle cx="8" cy="8" r="6.5" fill="none" stroke="#1664a8" stroke-width="1.6"/><path d="M1.5 8h13M8 1.5c-3 3.5-3 9.5 0 13M8 1.5c3 3.5 3 9.5 0 13" fill="none" stroke="#1664a8" stroke-width="1.2"/></svg>
        www.rtavenor.com
      </li>
      <li class="contact__item">
        <svg class="contact__icon" viewBox="0 0 16 16" aria-hidden="true"><rect x="1" y="3" width="14" height="10" rx="1.2" fill="#1664a8"/><path d="M1.5 3.8L8 9l6.5-5.2" fill="none" stroke="#ffffff" stroke-width="1.3"/></svg>
        MRT@RTavenor.com
      </li>
    </ul>
  </div>

  <p class="back__address">4187 Marlowe Ct. Cedar Hollow, Vermont 27614</p>
</section>

</body>
</html>
```